Design a building access mobile app for Quillo by Tamberlin Entry Systems

Hello, We're looking for an awesome designer to create an app design for our app Quillo, by Tamberlin Entry Systems. the mobile app allows employees open their office doors with their mobile phone. this means they don't have to use those plastic card badges or keys. We like clean modern design, dark and light themes. We don't have a logo yet.
Updates

Reason: Waiting on a couple designers to submit concepts

Target Market(s)

Commercial and employees

Industry/Entity Type

Building

Font styles to use
Sans Serif
Other font styles liked:
• Oswald extra light

Requirements
Must have
• nice clean design

```html
<!DOCTYPE html>
<html lang="en">
<head>
<meta charset="UTF-8">
<title>Tamberlin Security – Welcome Screen</title>
<link rel="stylesheet" href="https://fonts.googleapis.com/css2?family=Montserrat:wght@400;500;600;700&display=swap">
<style>
  :root {
    --board-bg: #e3e8f1;
    --header-bg: #ffffff;
    --ink: #111111;
    --ink-soft: #333333;
    --screen-dark: #17171a;
    --accent: #17a8ff;
    --white: #ffffff;
    --muted: #8a8a8e;
  }
  * { box-sizing: border-box; margin: 0; padding: 0; }
  html, body {
    width: 800px;
    height: 1200px;
    overflow: hidden;
    background: var(--board-bg);
    font-family: "Montserrat", Arial, sans-serif;
  }
  .board { position: relative; width: 800px; height: 1200px; }

  .board-header {
    height: 64px;
    background: var(--header-bg);
    display: flex;
    align-items: center;
    justify-content: space-between;
    padding: 0 18px;
  }
  .board-title { font-size: 26px; font-weight: 500; color: var(--ink); letter-spacing: 0.3px; }
  .board-meta { font-size: 18px; font-weight: 500; color: var(--ink-soft); }

  .screen {
    position: absolute;
    left: 100px;
    top: 92px;
    width: 600px;
    height: 1067px;
    overflow: hidden;
    background: var(--screen-dark);
    box-shadow: 0 4px 10px rgba(0,0,0,0.18);
  }
  .screen-photo {
    position: absolute;
    inset: 0;
    background:
      radial-gradient(ellipse at 60% 10%, rgba(110,40,45,0.35), transparent 55%),
      radial-gradient(ellipse at 55% 50%, rgba(90,80,80,0.35), transparent 50%),
      radial-gradient(ellipse at 40% 75%, rgba(70,65,65,0.4), transparent 55%),
      linear-gradient(180deg, #1b1a1d 0%, #222124 50%, #161618 100%);
  }

  .brand-mark {
    position: absolute;
    left: 50px;
    top: 230px;
    display: flex;
    align-items: center;
    gap: 14px;
  }
  .brand-square { width: 28px; height: 28px; background: var(--accent); }
  .brand-name { font-size: 40px; font-weight: 700; color: var(--white); }

  .welcome {
    position: absolute;
    left: 49px;
    top: 324px;
    text-transform: uppercase;
    font-size: 31px;
    font-weight: 500;
    line-height: 39px;
    letter-spacing: 0.5px;
  }
  .welcome-kicker { color: var(--accent); }
  .welcome-title { color: var(--white); }

  .btn {
    position: absolute;
    left: 40px;
    width: 520px;
    border-radius: 44px;
    display: flex;
    align-items: center;
    justify-content: center;
    font-size: 23px;
    font-weight: 700;
    color: var(--white);
  }
  .btn-login { top: 717px; height: 88px; background: var(--accent); }
  .btn-signup { top: 830px; height: 87px; border: 1.5px solid var(--white); }

  .help-link {
    position: absolute;
    right: 40px;
    top: 968px;
    font-size: 22px;
    font-weight: 500;
    color: var(--muted);
    letter-spacing: 0.4px;
  }
</style>
</head>
<body>
<main class="board">
  <header class="board-header">
    <h1 class="board-title">Tamberlin Security</h1>
    <span class="board-meta">Version 1 / 7 Screens</span>
  </header>

  <section class="screen">
    <div class="screen-photo" role="img" aria-label="Darkened photo of hands holding a smartphone"></div>

    <div class="brand-mark">
      <span class="brand-square"></span>
      <span class="brand-name">Tamberlin</span>
    </div>

    <div class="welcome">
      <p class="welcome-kicker">Welcome</p>
      <p class="welcome-title">Tamberlin Security</p>
    </div>

    <div class="btn btn-login">Log in</div>
    <div class="btn btn-signup">Sign up</div>

    <span class="help-link">Need Help?</span>
  </section>
</main>
</body>
</html>
```